KAJU Freightways #ALLKAJU Business Cards & Letterhead

I am looking to business cards designed for our organization. We are currently undergoing a small re-branding that is taking place. Our organization is called KAJU Freightways and we are headquartered in Phoenix, AZ. We primarily provide transportation and logistics services to the Marlow Parcel Bureau who is our largest customer. I would like to see a design that incorporates name, title, contact info, website, and address (this will be different depending on the employee). I would also like to see some color on the business card using our logo colors or a variation. I would like our logo on the back of the business card with the website displayed. The final design should communicate that we are a next generation transportation operate that focuses on being driver-first, customer-centric, innovative, and sustainable.We would also like our #ALLKAJU catch phrase incorporated as well.

Target Market(s)

Transportation & Logistics

Industry/Entity Type

Trucking Company

Contact Information for Business Card

-First and Last Name
-Position Title
-Contact Phone
-Contact Email
-Physical Address

Font styles to use
Serif

Colors

Designer to choose colors to be used in the design.

Requirements
Must have
• -KAJU logo prominently displayed
• -#ALLKAJU catch phrase used
• -Some amount of color, design gradient, etc.
• -Logo on the back with website listed (https://www.kajufreightco.example)

```html
<!DOCTYPE html>
<html lang="en">
<head>
<meta charset="utf-8">
<title>KAJU Freightways Business Card</title>
<link rel="stylesheet" href="https://fonts.googleapis.com/css2?family=Lora:wght@400;500;700&family=Playfair+Display:wght@700&display=swap">
<style>
  :root {
    --backdrop: #1b1b1b;
    --card: #222222;
    --card-edge: #2b2b2b;
    --green: #6cc23a;
    --white: #f4f4f4;
  }
  * { margin: 0; padding: 0; box-sizing: border-box; }
  html, body { width: 1200px; height: 900px; overflow: hidden; }
  body {
    background: radial-gradient(ellipse at 60% 30%, #2c2c2c 0%, var(--backdrop) 70%);
    font-family: "Lora", serif;
    color: var(--white);
    display: flex;
    flex-direction: column;
    align-items: center;
    justify-content: center;
    gap: 40px;
  }
  .card {
    width: 640px;
    height: 366px;
    background: linear-gradient(135deg, var(--card) 0%, var(--card) 55%, #303030 85%, var(--card-edge) 100%);
    box-shadow: 0 14px 30px rgba(0,0,0,0.55);
    position: relative;
  }
  /* Front */
  .card-front {
    display: flex;
    flex-direction: column;
    align-items: center;
    justify-content: center;
  }
  .brand {
    display: flex;
    align-items: center;
    gap: 16px;
    margin-top: -10px;
  }
  .brand-dot {
    width: 30px;
    height: 30px;
    border-radius: 50%;
    background: var(--green);
  }
  .brand-name {
    font-family: "Lora", serif;
    font-weight: 700;
    font-size: 64px;
    letter-spacing: 2px;
    color: var(--white);
  }
  .tagline {
    margin-top: 8px;
    font-size: 16px;
    font-weight: 500;
    letter-spacing: 4px;
    color: var(--green);
  }
  .front-web {
    position: absolute;
    bottom: 34px;
    left: 0; right: 0;
    text-align: center;
    font-size: 17px;
    font-weight: 500;
    letter-spacing: 2.5px;
  }
  /* Back */
  .identity {
    position: absolute;
    left: 30px;
    top: 120px;
    width: 290px;
    text-align: right;
  }
  .person-name {
    font-family: "Playfair Display", serif;
    font-weight: 700;
    font-size: 26px;
    color: var(--green);
    text-transform: uppercase;
    line-height: 1.15;
    white-space: nowrap;
  }
  .person-title {
    font-size: 17px;
    margin-top: 4px;
  }
  .divider {
    position: absolute;
    left: 336px;
    top: 120px;
    width: 2px;
    height: 76px;
    background: var(--green);
  }
  .contacts {
    position: absolute;
    left: 356px;
    top: 120px;
    list-style: none;
    font-size: 16px;
    line-height: 26px;
  }
  .contacts li { display: flex; align-items: center; gap: 10px; white-space: nowrap; }
  .contacts svg { width: 12px; height: 12px; flex: none; }
  .web-accent { color: var(--green); }
  .address {
    position: absolute;
    left: 60px;
    bottom: 42px;
    font-size: 17px;
    letter-spacing: 0.4px;
  }
</style>
</head>
<body>
  <section class="card card-front">
    <div class="brand">
      <span class="brand-dot"></span>
      <span class="brand-name">KAJU</span>
    </div>
    <p class="tagline">#ALLKAJU</p>
    <p class="front-web">www.kajufreightco.example</p>
  </section>

  <section class="card card-back">
    <div class="identity">
      <h1 class="person-name">Darren Holloway</h1>
      <p class="person-title">Director</p>
    </div>
    <span class="divider"></span>
    <ul class="contacts">
      <li>
        <svg viewBox="0 0 12 12" aria-hidden="true"><path d="M2.5 1 L4.5 1 L5 3.5 L3.8 4.3 C4.4 5.8 5.9 7.3 7.5 8 L8.3 6.8 L11 7.3 L11 9.5 C11 10.3 10.3 11 9.5 11 C5 10.6 1.4 7 1 2.5 C1 1.7 1.7 1 2.5 1 Z" fill="#6cc23a"/></svg>
        602-555-0148
      </li>
      <li>
        <svg viewBox="0 0 12 12" aria-hidden="true"><rect x="1" y="2.5" width="10" height="7" fill="none" stroke="#6cc23a" stroke-width="1.2"/><path d="M1 2.5 L6 6.5 L11 2.5" fill="none" stroke="#6cc23a" stroke-width="1.2"/></svg>
        info@kajufreightco.example
      </li>
      <li>
        <svg viewBox="0 0 12 12" aria-hidden="true"><circle cx="6" cy="6" r="5" fill="none" stroke="#6cc23a" stroke-width="1.1"/><ellipse cx="6" cy="6" rx="2.2" ry="5" fill="none" stroke="#6cc23a" stroke-width="1"/><path d="M1 6 H11" stroke="#6cc23a" stroke-width="1"/></svg>
        <span>www.<span class="web-accent">kajufreightco</span>.example</span>
      </li>
    </ul>
    <p class="address">4170 North Canyon Ridge Road Phoenix, AZ 85027</p>
  </section>
</body>
</html>
```